Bramble Hounds Dog Behaviour, Training and Natural Healthcare Website

Hey there,
I need a webpage designed for my new business. It needs to be something authentic, new, fresh and representative of my business ethos. I operate out of Newcastle, NSW. I believe my job is to keep dogs alive and in their home by promoting communication and connection between dogs and their owners. This can't be achieved through training and behaviour alone. Nutritional guidance and environmental adaptation are often needed to complete the package and increase the success rate for these programs. I provide practical services such as walking coaching, nutrition profiling, behavioural modification, puppy minding, board and train programs for puppies and young dogs, training, basic and complex skills training, physical therapies and natural healthcare options. In effect taking care of the whole dog.
My motto is = Happy dogs, happy owners.
My catch cry is = promoting communication and connection between dogs and their owners.

I have in mind pages that can also link to other pages when an icon is clicked. I need a homepage, sections to explain what each of my services do (4 - which could be independent pages so I can attach photos) and a gallery. I want to have multi page function, an online capability for future retail, ability to amend and update content myself, an online booking and payment facility. My interests lie in I have seen many successes via and environmental modifications.
I've attached the logo which features prominently on my business card and Facebook page. The corporate colours are Blue with a splash of red and white. The dog being held in the healing hands must feature.

Thanks!

Target Market(s)

Australian Pet Dog Owners

Industry/Entity Type

Communication

Coding

Colors
0355a3
ec1f27
ffffff

Requirements
Must have
• The business colours (blue with a splash of red and white), the dog in the healing hands
Should not have
• Pawprints or cartoon animals

```html
<!DOCTYPE html>
<html lang="en">
<head>
<meta charset="utf-8">
<title>Bramble Hounds – Dog Behaviour, Training and Natural Healthcare</title>
<link rel="stylesheet" href="https://fonts.googleapis.com/css2?family=Arimo:wght@400;700&family=Open+Sans:wght@400;600&display=swap">
<style>
:root{
  --blue:#0355a3;
  --blue-light:#1b8ee0;
  --blue-dark:#0a4aa0;
  --red:#ec1f27;
  --white:#ffffff;
  --ink:#333333;
  --muted:#555555;
  --rule:#d9d9d9;
  --panel:#f4f4f4;
}
*{box-sizing:border-box;margin:0;padding:0}
html,body{width:709px;height:1200px;overflow:hidden}
body{position:relative;background:var(--white);font-family:Arimo,Arial,sans-serif;color:var(--ink)}
.abs{position:absolute}
a{color:inherit;text-decoration:none}

/* header */
.site-header{left:0;top:0;width:709px;height:85px;background:linear-gradient(180deg,var(--blue-light) 0%,var(--blue) 100%)}
.brand-mark{left:86px;top:4px;width:52px;height:52px;border-radius:50%;background:var(--white);border:3px solid var(--red)}
.brand-name{left:20px;top:56px;width:136px;text-align:center;color:var(--white);font-weight:700;font-size:13px;letter-spacing:.3px}
.brand-tagline{left:20px;top:72px;width:136px;text-align:center;color:var(--white);font-size:7px}
.header-social{left:518px;top:28px;display:flex;gap:9px}
.header-social span,.footer-social span{width:10px;height:10px;border-radius:50%;background:var(--white);display:block}
.contact-btn{left:597px;top:25px;width:75px;height:18px;background:var(--white);color:var(--blue);font-size:7px;text-align:center;line-height:18px}
.main-nav{left:366px;top:59px;display:flex;font-size:7.5px;color:var(--white)}
.main-nav a{padding:0 9px;height:15px;line-height:15px}
.main-nav a.active{border:1px solid var(--white);border-radius:2px;padding:0 12px;margin-right:1px}

/* hero */
.hero{left:0;top:85px;width:709px;height:318px;background:linear-gradient(180deg,#3d5a2a 0%,#6f8a3c 45%,#8e7a55 80%,#a08c6a 100%)}
.hero-shadow{left:20px;top:403px;width:669px;height:14px;background:radial-gradient(ellipse at top,rgba(0,0,0,.18),rgba(0,0,0,0) 70%)}
.hero-caption{left:361px;top:194px;width:330px;height:152px;background:rgba(30,30,30,.72);color:var(--white);text-align:right;padding:8px 18px 0 10px;font-family:"Open Sans",sans-serif;overflow:hidden}
.hero-caption h1{font-weight:400;font-size:26px;line-height:32px;white-space:nowrap}
.hero-caption h2{font-weight:400;font-size:12.4px;line-height:17px;margin-top:4px;white-space:nowrap}
.hero-caption p{font-size:8.6px;line-height:12px;margin-top:12px}
.slide-prev{left:650px;top:359px;width:17px;height:17px}
.slide-next{left:672px;top:359px;width:17px;height:17px}

/* about */
.section-title{font-size:16px;font-weight:400;color:#222}
.about-title{left:38px;top:430px}
.body-text{font-size:7.2px;line-height:11.4px;color:var(--muted)}
.about-intro{left:36px;top:460px;width:415px}
.about-image{left:39px;top:500px;width:149px;height:99px;background:linear-gradient(135deg,#f3f3f3,#d8d2c8)}
.about-side{left:198px;top:499px;width:247px;text-align:justify}
.about-more{left:39px;top:612px;width:407px;text-align:justify}
.btn-red{background:var(--red);color:var(--white);text-align:center}
.about-btn{left:350px;top:670px;width:96px;height:21px;line-height:21px;font-size:9px}

/* services */
.services-title{left:478px;top:430px}
.services-sub{left:478px;top:455px;font-size:7px;color:#444}
.service-row{left:478px;width:194px;height:20px;border-bottom:1px solid var(--rule);font-size:8.5px;color:#333;line-height:20px}
.service-row .toggle{position:absolute;right:0;top:2px;width:18px;height:18px;background:#ddd;color:#333;text-align:center;line-height:17px;font-weight:700;font-size:10px}
.service-desc{left:478px;top:508px;width:194px}
.service-btn{left:478px;top:561px;width:57px;height:18px;line-height:18px;font-size:8.5px}

.divider{left:38px;top:714px;width:637px;height:1px;background:var(--rule)}

/* news */
.news{left:34px;top:746px;width:640px;height:69px;background:var(--panel)}
.news-label{left:34px;top:746px;width:152px;height:69px;background:linear-gradient(180deg,#2478cf,var(--blue-dark));color:var(--white);font-size:16px;line-height:69px;padding-left:29px}
.news-image{left:209px;top:758px;width:61px;height:46px;background:radial-gradient(circle at 50% 45%,#9a5b2b,#6b3e1e 60%,#e9e6e0 62%)}
.news-title{left:291px;top:754px;font-size:13px;color:#444;font-weight:400}
.news-text{left:291px;top:775px;width:360px;font-size:7px;line-height:10.4px;color:#555}
.news-link{left:601px;top:799px;font-size:7px;color:var(--red)}

/* testimonials */
.testimonials-title{left:38px;top:857px}
.t-nav{top:859px}
.t-card{top:893px;width:186px;height:63px;background:var(--white);box-shadow:0 0 3px rgba(0,0,0,.18);padding:12px 24px 10px 10px;font-family:"Open Sans",sans-serif;font-size:7.2px;line-height:12px;color:#555}
.t-card:after{content:"";position:absolute;left:10px;bottom:-7px;border-left:7px solid var(--white);border-bottom:7px solid transparent}
.t-split{top:893px;width:1px;height:100px;background:var(--rule)}
.t-avatar{top:973px;width:32px;height:32px;border-radius:50%;background:linear-gradient(135deg,#c9a98e,#7b5a45)}
.t-name{top:985px;font-family:"Open Sans",sans-serif;font-size:7px;color:#555}
.dot{top:1030px;width:7px;height:7px;border-radius:50%;border:1px solid var(--red)}
.dot.on{background:var(--red)}

/* footer */
.site-footer{left:0;top:1088px;width:709px;height:112px;background:linear-gradient(180deg,var(--blue) 0%,#1a73d0 100%)}
.footer-nav{left:36px;top:1110px;display:flex;font-size:7.5px;color:var(--white)}
.footer-nav a{height:18px;line-height:18px;padding:0 6px;margin-right:5px}
.footer-nav a.active{border:1px solid var(--white);border-radius:9px;padding:0 5px}
.footer-social{left:612px;top:1112px;display:flex;gap:9px}
.footer-tip{left:614px;top:1131px;width:42px;height:14px;border-radius:7px;background:var(--white);color:var(--blue);font-size:6px;font-weight:700;text-align:center;line-height:14px}
.f-text{font-size:6px;color:var(--white);line-height:8px}
.copyright{left:526px;top:1166px;font-size:6.2px;color:var(--white)}
</style>
</head>
<body>

<header class="site-header abs"></header>
<div class="brand-mark abs" aria-hidden="true"></div>
<div class="brand-name abs">BRAMBLE HOUNDS</div>
<div class="brand-tagline abs">HAPPY DOGS, HAPPY OWNERS</div>
<div class="header-social abs" aria-label="Social links"><span></span><span></span><span></span><span></span></div>
<a class="contact-btn abs" href="#">CONTACT</a>
<nav class="main-nav abs">
  <a class="active" href="#">HOME</a><a href="#">ABOUT US</a><a href="#">SERVICE</a><a href="#">PRODUCTS</a><a href="#">BLOG</a><a href="#">TESTIMONIALS</a>
</nav>

<div class="hero abs" role="img" aria-label="Photo of a trainer in a forest clearing working with a black labrador"></div>
<div class="hero-shadow abs"></div>
<div class="hero-caption abs">
  <h1>Bramble Hounds</h1>
  <h2>We are Dog behaviour study and training company</h2>
  <p>Vestibulum pretium, nisi vel convallis convallis, mi turpis feugiat leo, posuere feugiat nisl risus at erat. Cum sociis natoque penatibus et magnis dis parturient montes, nascetur ridiculus mus. Aliquam at cursus nisl. Duis nec odio mi. Donec lacinia lectus at bibendum volutpat. Donec vestibulum sem quis consectetur aliquet.</p>
</div>
<svg class="slide-prev abs" viewBox="0 0 17 17"><circle cx="8.5" cy="8.5" r="8.5" fill="#fff"/><path d="M10 5 6.5 8.5 10 12" fill="none" stroke="#888" stroke-width="1.6"/></svg>
<svg class="slide-next abs" viewBox="0 0 17 17"><circle cx="8.5" cy="8.5" r="8.5" fill="#0355a3"/><path d="M7 5l3.5 3.5L7 12" fill="none" stroke="#fff" stroke-width="1.6"/></svg>

<h3 class="section-title about-title abs">About Us</h3>
<p class="body-text about-intro abs">Vestibulum pretium, nisi vel convallis convallis, mi turpis feugiat leo, posuere feugiat nisl risus at erat. Cum sociis natoque penatibus et magnis dis parturient montes, nascetur ridiculus mus. Aliquam at cursus nisl. Duis nec odio mi. Donec lacinia lectus at bibendum volutpat. Donec vestibulum sem quis consectetur aliquet. Proin at nibh vitae diam sollicitudin bibendum.</p>
<div class="about-image abs" role="img" aria-label="Image of a dog bone treat"></div>
<p class="body-text about-side abs">Lorem ipsum dolor sit amet, consectetur adipiscing elit. Ut volutpat lacus eu dictum sagittis. Ut dictum vulputate augue nec euismod. Curabitur cursus magna ut turpis gravida sagittis. Nam ultrices tristique risus, condimentum dignissim lectus euismod a. Curabitur varius lacinia ex, sed volutpat nunc faucibus vel. Nullam justo mauris, ullamcorper nec rhoncus nec, scelerisque et lorem. Sed ut augue non risus efficitur pellentesque. Nam pulvinar nunc sapien,</p>
<p class="body-text about-more abs">Lorem ipsum dolor sit amet, consectetur adipiscing elit. Ut volutpat lacus eu dictum sagittis. Ut dictum vulputate augue nec euismod. Curabitur cursus magna ut turpis gravida sagittis. Nam ultrices tristique risus, condimentum dignissim lectus euismod a. Curabitur varius lacinia ex, sed volutpat nunc faucibus vel.</p>
<a class="btn-red about-btn abs" href="#">Read More</a>

<h3 class="section-title services-title abs">Our Services</h3>
<p class="services-sub abs">We wont let you down, we are here to make you feel..</p>
<div class="service-row abs" style="top:482px">Walking coaching<span class="toggle">&minus;</span></div>
<p class="body-text service-desc abs">Our management consulting services address our clienteles' crucial issues and opportunities: strategy, organizational structure, business development, operations, marketing and transformation.</p>
<a class="btn-red service-btn abs" href="#">Read More</a>
<div class="service-row abs" style="top:597px">Nutrition profiling<span class="toggle">+</span></div>
<div class="service-row abs" style="top:621px">Behavioural modification<span class="toggle">+</span></div>
<div class="service-row abs" style="top:644px">Puppy minding<span class="toggle">+</span></div>
<div class="service-row abs" style="top:667px">Training<span class="toggle">+</span></div>

<div class="divider abs"></div>

<div class="news abs"></div>
<div class="news-label abs">Latest News</div>
<svg class="abs" style="left:186px;top:770px" width="15" height="22" viewBox="0 0 15 22"><path d="M0 0 14 11 0 22Z" fill="#1766c0"/></svg>
<div class="news-image abs" role="img" aria-label="Bowl of dry dog food"></div>
<h4 class="news-title abs">Lorem ipsum dolor</h4>
<p class="news-text abs">Vestibulum pretium, nisi vel convallis convallis, mi turpis feugiat leo, posuere feugiat nisl risus at erat. Cum sociis natoque penatibus et magnis dis parturient montes, nascetur ridiculus mus. Aliquam at cursus nisl.</p>
<a class="news-link abs" href="#">Read More &gt;&gt;</a>

<h3 class="section-title testimonials-title abs">Client Testimonials</h3>
<svg class="t-nav abs" style="left:646px" width="12" height="12" viewBox="0 0 12 12"><path d="M11 0 0 6 11 12Z" fill="#c8c8c8"/></svg>
<svg class="t-nav abs" style="left:661px" width="12" height="12" viewBox="0 0 12 12"><path d="M1 0 12 6 1 12Z" fill="#0355a3"/></svg>

<div class="t-card abs" style="left:39px">From someone who never trained with music out on the road due to safety concerns I'm in love with the trailBuds. Great</div>
<div class="t-card abs" style="left:263px">Because I like my music loud, there is always a danger that I cannot hear traffic or other noises when training. The trailBuds allows</div>
<div class="t-card abs" style="left:488px">It's a completely different experience form riding with conventional headphones... The awareness, and where cars where coming</div>
<div class="t-split abs" style="left:242px"></div>
<div class="t-split abs" style="left:466px"></div>
<div class="t-avatar abs" style="left:39px" role="img" aria-label="Client portrait"></div>
<div class="t-name abs" style="left:78px">Lena Hartwell</div>
<div class="t-avatar abs" style="left:262px" role="img" aria-label="Client portrait"></div>
<div class="t-name abs" style="left:302px">Ruby Calder</div>
<div class="t-avatar abs" style="left:487px" role="img" aria-label="Client portrait"></div>
<div class="t-name abs" style="left:527px">Tom Brennick</div>
<span class="dot on abs" style="left:334px"></span>
<span class="dot abs" style="left:344px"></span>
<span class="dot abs" style="left:354px"></span>

<footer class="site-footer abs"></footer>
<nav class="footer-nav abs">
  <a class="active" href="#">HOME</a><a href="#">ABOUT US</a><a href="#">SERVICE</a><a href="#">PRODUCTS</a><a href="#">BLOG</a><a href="#">TESTIMONIALS</a>
</nav>
<div class="footer-social abs" aria-label="Social links"><span></span><span></span><span></span><span></span></div>
<div class="footer-tip abs">GALLERY</div>

<svg class="abs" style="left:36px;top:1163px" width="13" height="13" viewBox="0 0 13 13"><circle cx="6.5" cy="6.5" r="6.5" fill="#fff"/><path d="M3 7 6.5 3.8 10 7M4.3 6.2V9.5h4.4V6.2" fill="none" stroke="#0355a3" stroke-width="1.2"/></svg>
<div class="f-text abs" style="left:55px;top:1166px;font-weight:700">14 WATTLE LANE, MEREWETHER, NEWCASTLE NSW<br>2291, AUSTRALIA</div>
<svg class="abs" style="left:250px;top:1163px" width="13" height="13" viewBox="0 0 13 13"><circle cx="6.5" cy="6.5" r="6.5" fill="#fff"/><path d="M4.2 3.5c-.8.6-.6 2 .8 3.6s3 2.3 3.8 1.6l.6-.7-1.4-1.2-.7.5c-.6-.3-1.3-1-1.6-1.6l.5-.7-1.2-1.4z" fill="#0355a3"/></svg>
<div class="f-text abs" style="left:269px;top:1167px">+61 2 4960 3187</div>
<svg class="abs" style="left:333px;top:1163px" width="13" height="13" viewBox="0 0 13 13"><circle cx="6.5" cy="6.5" r="6.5" fill="#fff"/><rect x="3.5" y="4.5" width="6" height="4.2" fill="none" stroke="#0355a3" stroke-width="1"/><path d="M3.5 4.5 6.5 7l3-2.5" fill="none" stroke="#0355a3" stroke-width="1"/></svg>
<div class="f-text abs" style="left:352px;top:1166px;font-size:7px">hello@bramblehounds.org</div>
<div class="copyright abs">&copy;Copyright 2014 bramblehounds. All Rights Reserved.</div>

</body>
</html>
```